Philadelphia-based Nonprofit Needs Invitation Design for 11th Annual Cook-Off Fundraiser

Venture Hollow (VH) is a non-profit 501(c)(3) microenterprise development organization focused on growing businesses and jobs in our local communities. By connecting hundreds of entrepreneurs each year with access to capital, one-on-one technical assistance, business training and networking opportunities, Venture Hollow helps promising individuals to develop economic self-sufficiency and create job opportunities through business ownership.

The theme for our 11th annual Plate of Promise cook-off fundraiser, “Tastes from Around the World: Savor the Flavors,” reflects our commitment to fostering and celebrating the diverse network of entrepreneurs, business owners, and supporters that make VH’s work possible.

Plate of Promise is a chance for Venture Hollow to showcase the culinary talents of our entrepreneurs and business owners, while also hosting a fun-filled night with celebrity guest judges, delicious hors d'oeuvres and desserts, a silent auction, and an exciting cook-off contest.

We would like a double-sided, two-color folded invitation (fold size: 5" x 7"); a double-sided, two-color reply card (5” x 4”); a mailing envelope (A7 envelope, grayscale) and a reply envelope (A2 envelope, grayscale). For an example of the design that was on the cover of last year's invitation, see here: http://www.myventurehollow.example/sites/vh.brightquill.example/files/imagecache/250px_thumb/signature_images/VH_RiverBendSupper.png.

The final design should appeal to a broad range of potential attendees and be inviting and warm. While we send out a different invitation for each Plate of Promise fundraiser, we were very pleased with last year’s invitation (attached, “Plate of Promise Invitation_2011”) and would like an invitation design that is similar (for color scheme please refer to the web link in the above paragraph). A scanned copy of the reply card is also attached ("Plate of Promise Reply Cards 2011"). Finally a copy of the outer envelope is attached ("Plate of Promise Outer Envelope_2011").

Target Market(s)

Our target market includes: existing and past donors; local business owners; and entrepreneurs.

Industry/Entity Type

Non-Profit

Requirements
Must have
• - The main illustration on the invitation should be food-themed
- The invitation should include all of the copy in the attached word .doc ("Plate of Promise Invitation Copy_2013").
Should not have
• - Any designs, backgrounds or fonts that make the invitation difficult to read or understand

```html
<!DOCTYPE html>
<html lang="en">
<head>
<meta charset="utf-8">
<title>Plate of Promise 2013 Invitation</title>
<link href="https://fonts.googleapis.com/css2?family=Parisienne&family=Quicksand:wght@400;500;700&family=Source+Sans+3:wght@400&display=swap" rel="stylesheet">
<style>
  :root {
    --maroon: #943735;
    --maroon-light: #b0504d;
    --white: #ffffff;
    --ink: #111111;
    --ribbon: #c9c9c9;
    --ribbon-dark: #8f8f8f;
    --ribbon-line: #555555;
  }
  * { margin: 0; padding: 0; box-sizing: border-box; }
  html, body { width: 1200px; height: 857px; overflow: hidden; background: var(--white); }
  .invite { position: relative; width: 1200px; height: 857px; background: var(--white); overflow: hidden; }

  .side-panel {
    position: absolute; left: 0; top: 0; width: 600px; height: 857px;
    background: var(--maroon); color: var(--white); text-align: center;
    font-family: 'Quicksand', sans-serif;
  }
  .script-heading {
    position: absolute; left: 0; width: 600px;
    font-family: 'Parisienne', cursive; font-size: 36px; font-weight: 400; line-height: 1;
  }
  .judge { position: absolute; left: 0; width: 600px; }
  .judge-name { font-weight: 700; font-size: 27px; line-height: 34px; letter-spacing: 0.3px; }
  .judge-role { font-weight: 400; font-size: 25.5px; line-height: 36px; }

  .entertainment { position: absolute; left: 0; top: 480px; width: 600px; list-style: none; }
  .entertainment li { font-weight: 700; font-size: 26px; line-height: 34px; letter-spacing: 0.3px; }
  .entertainment .dot {
    width: 20px; height: 20px; border-radius: 50%; background: var(--white);
    margin: 6px auto 9px;
  }

  .ribbon { position: absolute; left: 620px; top: 20px; }

  .intro {
    position: absolute; left: 606px; top: 154px; width: 590px;
    font-family: 'Source Sans 3', sans-serif; font-size: 19px; line-height: 25.8px;
    color: var(--ink); text-align: center;
  }
  .intro p + p { margin-top: 25.8px; }

  .event-date, .event-time {
    position: absolute; font-family: 'Quicksand', sans-serif; font-weight: 700; color: var(--ink);
  }
  .event-date { left: 715px; top: 562px; font-size: 42px; line-height: 50px; }
  .event-time { left: 733px; top: 612px; font-size: 40px; line-height: 50px; }
  .event-date sup { font-size: 20px; vertical-align: 18px; }
  .event-time .small { font-size: 27px; }

  .venue {
    position: absolute; font-family: 'Quicksand', sans-serif; font-weight: 700; color: var(--ink);
    text-transform: uppercase; font-size: 24.5px; line-height: 30px; letter-spacing: 0.4px;
  }
  .venue-name { left: 650px; top: 663px; }
  .venue-city { left: 708px; top: 695px; }
  .address {
    position: absolute; font-family: 'Quicksand', sans-serif; font-weight: 700; color: var(--ink);
    font-variant: small-caps; font-size: 25px; line-height: 30px;
  }
  .address-street { left: 682px; top: 729px; }
  .address-city { left: 670px; top: 760px; }

  .utensil-art {
    position: absolute; left: 1022px; top: 712px; width: 160px; height: 145px;
    background: linear-gradient(180deg, var(--maroon-light), var(--maroon));
  }

  .web-band {
    position: absolute; left: 600px; top: 805px; width: 486px; height: 34px; z-index: 2;
    background: var(--maroon); color: var(--white);
    font-family: 'Quicksand', sans-serif; font-weight: 700; font-variant: small-caps;
    font-size: 22px; line-height: 34px; text-align: center; letter-spacing: 0.3px;
  }
</style>
</head>
<body>
<main class="invite">
  <section class="side-panel">
    <h2 class="script-heading" style="top:50px;">Featuring Special Guest Judges</h2>
    <div class="judge" style="top:102px;">
      <div class="judge-name">MARLA QUINCE</div>
      <div class="judge-role">Co-owner, Quince Street Kitchen</div>
    </div>
    <div class="judge" style="top:205px;">
      <div class="judge-name">THEO BRANNIGAN</div>
      <div class="judge-role">Executive Chef and co-owner, Cocina Brisa</div>
    </div>
    <div class="judge" style="top:308px;">
      <div class="judge-name">DALE HARTWELL</div>
      <div class="judge-role">Owner, Hartwell’s Engine House</div>
    </div>
    <h2 class="script-heading" style="top:425px;">Entertainement Includes</h2>
    <ul class="entertainment">
      <li>COOK-OFF CONTEST</li><li><div class="dot"></div></li>
      <li>SILENT AUCTION</li><li><div class="dot"></div></li>
      <li>HORS D’OEUVRES</li><li><div class="dot"></div></li>
      <li>OPEN BAR</li><li><div class="dot"></div></li>
      <li>THE PEOPLE’S CHOICE AWARD</li>
    </ul>
  </section>

  <svg class="ribbon" width="500" height="110" viewBox="0 0 500 110" aria-label="Plate of Promise 2013">
    <path d="M10 30 L40 40 L40 95 L10 85 L25 58 Z" fill="var(--ribbon-dark)" stroke="var(--ribbon-line)" stroke-width="1.5"/>
    <path d="M490 30 L460 40 L460 95 L490 85 L475 58 Z" fill="var(--ribbon-dark)" stroke="var(--ribbon-line)" stroke-width="1.5"/>
    <path d="M35 25 Q250 -5 465 25 L465 80 Q250 50 35 80 Z" fill="var(--ribbon)" stroke="var(--ribbon-line)" stroke-width="1.5"/>
    <path id="ribbon-arc" d="M45 68 Q250 38 457 68" fill="none"/>
    <text font-family="Quicksand, sans-serif" font-weight="700" font-size="33" fill="var(--maroon)" letter-spacing="0.5">
      <textPath href="#ribbon-arc" startOffset="50%" text-anchor="middle">PLATE OF PROMISE 2013</textPath>
    </text>
  </svg>

  <div class="intro">
    <p>Please join us for our 11th Annual Plate of Promise fundraiser and help us celebrate the achievements of our talented entrepreneurs.</p>
    <p>This year’s theme, “Tastes from Around the World: Savor the Flavors,” reflects our commitment to fostering and celebrating the diverse network of entrepreneurs, business owners, and supporters that make our work possible. The festivities will include our signature bake-off and cook-off competitions, where our innovative entrpreneurs compete for top prizes. Special guest judges - including Marla Quince, co-owner of Quince Street Kitchen, Theo Brannigan, executive chef and co-owner of Cocina Brisa, and Dale Hartwell, owner of Hartwell’s Engine House - will determine the winners. Don’t forget to bring your appetite to sample each contestant’s dish and vote for People’s Choice Award!</p>
  </div>

  <div class="event-date">Monday, April 29<sup>th</sup></div>
  <div class="event-time">6:00 <span class="small">PM</span> - 8:00<span class="small">PM</span></div>
  <div class="venue venue-name">Global Commons Hall</div>
  <div class="venue venue-city">Philadelphia</div>
  <div class="address address-street">4120 Linden Avenue</div>
  <div class="address address-city">Philadelphia, PA 19104</div>

  <div class="utensil-art" role="img" aria-label="Silhouette illustration of a spoon, fork and knife"></div>

  <div class="web-band">Visit us online at MyVentureHollow.example</div>
</main>
</body>
</html>
```